Bramblecrest Resource Group is a recycling company. We have started a marketing campaign and would love your artwork to help us get started. We would like the fallowing to be on our postcard:
At the top please write: Now servicing businesses in the city of Industry!
Below that we would like 3 pictures.. The first is a picture of trash, the second is a our logo and at plus sign. After that would be a picture of neat baled recycled material and the last picture would be money. Below this please right the following:
- Companies choose bramblecrest resource group because:
- if it can be recycled we will find a use for it
- we pay top dollar
- starting our service is fast and easy
* All it takes is one call/email and we will handle the rest
At the bottom please put our contact information
- 800.514.2976
- delphine@bramble722.com
- bramble722.com

Thanks guys! I have attached our logo!

I am sorry for this late post,but could you not put anything on the back except for a return address which is 4187 Tillery Ave Costa Mesa, Ca 92871 Thank you! We have had a lot of trouble in the past with the post office when we put stuff on the back for some reason.

Recycling

```html
<!DOCTYPE html>
<html lang="en">
<head>
<meta charset="utf-8">
<title>Bramblecrest Resource Group – Postcard</title>
<link href="https://fonts.googleapis.com/css2?family=Oxygen:wght@300;400;700&family=Alegreya+Sans+SC:wght@700&display=swap" rel="stylesheet">
<style>
  :root{
    --page:#ecebe8;
    --card:#e9eae7;
    --card-light:#f3f4f1;
    --panel:#c6c7c4;
    --panel-soft:#d3d4d1;
    --strip:#d4d5d2;
    --rule:#b4b5b2;
    --ink:#4b4c4a;
    --ink-soft:#6a6b69;
    --green:#5aa637;
    --green-pale:#d6e3cd;
  }
  *{box-sizing:border-box;margin:0;padding:0}
  html,body{width:1200px;height:900px;overflow:hidden}
  body{background:var(--page);font-family:"Oxygen",sans-serif;color:var(--ink);position:relative}

  .postcard{position:absolute;left:300px;width:600px;height:400px;overflow:hidden;
    box-shadow:0 2px 8px rgba(0,0,0,.12)}
  .postcard--front{top:40px;background:linear-gradient(160deg,var(--card-light) 0%,var(--card) 55%,#dfe0dd 100%)}
  .postcard--back{top:460px;background:linear-gradient(165deg,#f6f7f5 0%,#e6e7e4 70%,#dadbd8 100%)}

  /* front – left column */
  .sidebar{position:absolute;left:0;top:0;width:210px;height:400px;background:var(--panel-soft)}
  .brand{position:absolute;left:0;top:0;width:210px;height:78px;background:var(--panel);
    display:flex;align-items:center;gap:10px;padding:0 16px}
  .brand__dot{width:18px;height:18px;border-radius:50%;background:var(--green);flex:none}
  .brand__name{font-weight:700;font-size:17px;line-height:1.1;color:var(--ink-soft)}
  .tagline{position:absolute;right:22px;top:92px;text-align:right;font-size:15px;line-height:19px;color:var(--ink-soft)}
  .tagline .accent{color:var(--green)}
  .sidebar__rule{position:absolute;left:0;top:180px;width:210px;height:1px;background:var(--rule)}
  .contact{position:absolute;left:0;top:198px;width:210px;list-style:none;text-align:center;font-size:11px;letter-spacing:.6px;color:var(--ink-soft)}
  .contact li{margin-bottom:13px}
  .contact__icon{display:block;margin:0 auto 3px;width:17px;height:17px}

  /* front – right area */
  .bands{position:absolute;left:210px;top:0}
  .reasons-title{position:absolute;left:238px;top:20px;font-size:15px;line-height:18px;color:var(--ink-soft)}
  .reasons-title .accent{color:var(--green)}
  .reason{position:absolute;left:222px;height:20px;line-height:20px;padding:0 10px;font-size:12.5px;color:var(--ink-soft);
    background:linear-gradient(90deg,var(--strip) 0%,rgba(212,213,210,.6) 70%,rgba(212,213,210,0) 100%)}
  .reason--1{top:112px;width:300px}
  .reason--2{top:150px;width:230px}
  .reason--3{top:190px;width:260px}
  .closing{position:absolute;left:222px;top:248px;font-size:17px;line-height:21px;color:var(--ink)}
  .closing span{display:inline-block;padding:0 8px;background:linear-gradient(90deg,var(--strip),rgba(212,213,210,0))}

  .visual{position:absolute;left:490px;width:98px;height:98px;border-radius:50%;overflow:hidden;
    border:2px solid #f7f7f5;box-shadow:0 1px 4px rgba(0,0,0,.18)}
  .visual--bin{top:60px;background:radial-gradient(circle at 50% 45%,#3f8a35 0 26%,#e2e3e0 27% 100%)}
  .visual--mix{top:168px;background:linear-gradient(180deg,#e5e6e3 0%,#f0f0ee 100%)}
  .visual__pile{position:absolute;left:18px;top:14px;width:58px;height:24px;border-radius:10px;background:linear-gradient(90deg,#9aa38f,#6d7e8c,#b5b1a2)}
  .visual__plus{position:absolute;left:0;top:36px;width:100%;text-align:center;font-size:22px;font-weight:700;color:var(--ink)}
  .visual--cash{top:276px;background:radial-gradient(ellipse at 50% 50%,#a7b39a 0 32%,#e3e4e1 33% 100%)}

  /* back */
  .back-brand{position:absolute;left:24px;top:20px;display:flex;align-items:center;gap:8px}
  .back-brand .brand__dot{width:14px;height:14px}
  .back-brand .brand__name{font-size:14px}
  .back-lines{position:absolute;left:0;top:0}
  .stamp-box{position:absolute;right:18px;top:16px;width:60px;height:44px;border:1px solid #9c9d9a;
    font-size:6.5px;line-height:9px;text-align:center;color:var(--ink-soft);padding-top:4px;letter-spacing:.3px}
  .return-address{position:absolute;left:370px;top:205px;font-family:"Alegreya Sans SC",sans-serif;font-weight:700;
    font-size:19px;line-height:20px;color:var(--green);font-style:normal}
  .badge{position:absolute;border-radius:50%;background:var(--green-pale);border:2px solid #f5f6f3;box-shadow:0 1px 3px rgba(0,0,0,.12)}
  .badge--cash{left:212px;top:92px;width:84px;height:84px}
  .badge--mix{left:154px;top:170px;width:74px;height:74px}
  .badge--bin{left:84px;top:250px;width:64px;height:64px}
</style>
</head>
<body>

<section class="postcard postcard--front" aria-label="Postcard front">
  <svg class="bands" width="390" height="400" viewBox="0 0 390 400" aria-hidden="true">
    <polygon points="0,0 130,0 390,220 390,300" fill="#ffffff" opacity=".35"/>
    <polygon points="0,250 390,120 390,160 0,330" fill="#d9dad7" opacity=".5"/>
    <polygon points="60,400 390,330 390,400" fill="#d2d3d0" opacity=".5"/>
  </svg>

  <aside class="sidebar">
    <div class="brand">
      <span class="brand__dot"></span>
      <span class="brand__name">Bramblecrest Resource Group</span>
    </div>
    <p class="tagline">
      <span class="accent">Now servicing</span><br>
      businesses<br>
      in the city of<br>
      <span class="accent">Industry!</span>
    </p>
    <div class="sidebar__rule"></div>
    <ul class="contact">
      <li>
        <svg class="contact__icon" viewBox="0 0 20 20" aria-hidden="true"><circle cx="10" cy="10" r="10" fill="#e8e9e6"/><path d="M7 5c1 0 1.5 2 1.5 2.5S7.5 8.5 7.8 9.5s1.6 2.5 2.5 2.8 1.4-.8 1.9-.8 2.3.6 2.3 1.6-1.2 1.9-2.2 1.8C9.5 14.6 5.6 10.8 5.3 8 5.2 6.5 6 5 7 5z" fill="var(--green)"/></svg>
        800.514.2976
      </li>
      <li>
        <svg class="contact__icon" viewBox="0 0 20 20" aria-hidden="true"><circle cx="10" cy="10" r="10" fill="#e8e9e6"/><text x="10" y="14" text-anchor="middle" font-size="12" font-weight="700" fill="var(--green)" font-family="Oxygen,sans-serif">@</text></svg>
        DELPHINE@BRAMBLE722.COM
      </li>
      <li>
        <svg class="contact__icon" viewBox="0 0 20 20" aria-hidden="true"><circle cx="10" cy="10" r="10" fill="#e8e9e6"/><circle cx="10" cy="10" r="5.5" fill="none" stroke="var(--green)" stroke-width="1.4"/><ellipse cx="10" cy="10" rx="2.3" ry="5.5" fill="none" stroke="var(--green)" stroke-width="1.1"/><line x1="4.5" y1="10" x2="15.5" y2="10" stroke="var(--green)" stroke-width="1.1"/></svg>
        BRAMBLE722.COM
      </li>
    </ul>
  </aside>

  <p class="reasons-title">Companies choose<br>Bramblecrest <span class="accent">Resource</span> Group<br>because:</p>
  <p class="reason reason--1">if it can be recycled we will find a use for it</p>
  <p class="reason reason--2">we pay top dollar</p>
  <p class="reason reason--3">starting our service is fast and easy</p>
  <p class="closing"><span>All it takes is one call/email</span><br><span>and we will handle the rest</span></p>

  <div class="visual visual--bin" role="img" aria-label="Green recycling bin"></div>
  <div class="visual visual--mix">
    <div class="visual__pile" role="img" aria-label="Pile of mixed recyclable waste"></div>
    <div class="visual__plus">+</div>
  </div>
  <div class="visual visual--cash" role="img" aria-label="Stacks of banknotes"></div>
</section>

<section class="postcard postcard--back" aria-label="Postcard back">
  <svg class="back-lines" width="600" height="400" viewBox="0 0 600 400" aria-hidden="true">
    <polygon points="0,120 600,40 600,90 0,190" fill="#ffffff" opacity=".4"/>
    <polygon points="120,400 600,230 600,300 260,400" fill="#d3d4d1" opacity=".45"/>
    <line x1="330" y1="20" x2="330" y2="380" stroke="#cfd0cd" stroke-width="1"/>
  </svg>
  <div class="back-brand">
    <span class="brand__dot"></span>
    <span class="brand__name">Bramblecrest Resource Group</span>
  </div>
  <div class="stamp-box">PRESORTED<br>STANDARD<br>POSTAGE PAID</div>
  <div class="badge badge--cash" role="img" aria-label="Stacks of banknotes"></div>
  <div class="badge badge--mix" role="img" aria-label="Recyclable waste plus company name"></div>
  <div class="badge badge--bin" role="img" aria-label="Recycling bin"></div>
  <address class="return-address">4187 Tillery Ave Costa Mesa<br>Ca<br>92871</address>
</section>

</body>
</html>
```